Design my site www.brieflyledger.com

So here is what I am thinking in terms of design:

https://plenvo.com

https://www.skyluxair.com

http://kalvex.com/harbor-plaza-tower/

I want the theme to be white and blue (royal blue). I attached a paint picture of what I would like the site to look like in terms of placing the text. Generally, what I like about the sites above is that they are simple, you can navigate easily and have some kind of idea of what's going on by looking at the center (picture and motto). Let's establish a clear understanding of how the functional part of the site would look like. Please see the picture attached.

I want to keep it simple: On top would be the Name 'BRIEFLY ledger", somewhere to the right on top on the page would be 'Sign in" button.

In the center would be a picture (maybe a video) with the Motto (on top of it all in capital) OBSERVE NAVIGATE DECIDE and below would be the "sign up now"

Below the picture (like on kalvex.com site) or to the left on top of the page would be "About Us', "Press" "Contact Us' buttons.

Then once the user gets to his page his got 3 tabs " Press Headlines", "Events", " Briefings".

we would keep the same format I only have on the site, but separate for every Tab.

I do not want the user to get distracted. I also want him to be able to access the page though mobile phone and be able to get automatic updates just like Zorvan Pings without having to sign in daily.

The landing page must be minimalist yet with business/corporate feel where users can navigate easily and a "what you see is what you get" approach. You want an image or video (personally I prefer the video.. it does capture the users attention instantly, as long as it is an interesting video), with your taglines in it.

Sections available to public: About Us, Contact Us, Landing Page with Signup Option

Private: Public Sections + User Account Page, Tabs for (Events, Press Headlines, Briefings)

Target Market(s)

PR/media monitoring/diplomatic community

Coding

Coded - Design and coding required

Number of Pages Required

1 page

Font styles to use
Serif
Sans Serif

Colors
0255a3
ec1f27

Requirements
Must have
• a simple landing page, that is user friendly.
Nice to have
• a video with the explanation of how to navigate the site
Should not have
• too many colors, graphs etc.

```html
<!DOCTYPE html>
<html lang="en">
<head>
<meta charset="utf-8">
<title>Briefly Ledger</title>
<link href="https://fonts.googleapis.com/css2?family=Arimo:wght@700&family=Archivo:wght@800&family=Open+Sans:wght@400&display=swap" rel="stylesheet">
<style>
:root{
  --royal:#0255a3;
  --ink:#222222;
  --body-text:#555555;
  --white:#ffffff;
  --tab-dark:#121212;
  --tab-line:#3a3a3a;
  --sea-deep:#1d5c8c;
  --sea-light:#4f8fb4;
  --city-grey:#8e9499;
  --city-dark:#5b6266;
}
*{box-sizing:border-box;margin:0;padding:0}
html,body{width:1041px;height:1200px;overflow:hidden;background:var(--white)}
body{position:relative;font-family:"Open Sans",Arial,sans-serif}

.site-header{position:absolute;top:0;left:0;width:1041px;height:72px;border-top:3px solid var(--royal);background:var(--white)}
.brand{position:absolute;left:86px;top:26px;font-family:"Arimo",Arial,sans-serif;font-weight:700;font-size:18px;color:var(--ink);letter-spacing:0.2px}
.sign-in{position:absolute;left:865px;top:16px;width:90px;height:38px;background:var(--royal);border-radius:3px;color:var(--white);font-family:"Arimo",Arial,sans-serif;font-weight:700;font-size:14px;display:flex;align-items:center;justify-content:center;gap:6px}

.hero{position:absolute;top:72px;left:0;width:1041px;height:434px;overflow:hidden}
.hero-visual{position:absolute;inset:0;background:linear-gradient(180deg,#5f8fb0 0%,var(--sea-deep) 14%,var(--sea-light) 34%,#6d8a86 48%,var(--city-grey) 62%,#7d8588 78%,var(--city-dark) 100%)}
.play{position:absolute;left:497px;top:70px}
.motto{position:absolute;left:0;top:148px;width:1041px;text-align:center;font-family:"Archivo",Arial,sans-serif;font-weight:800;font-size:48px;color:var(--white);letter-spacing:0.5px;line-height:1}
.sign-up{position:absolute;left:427px;top:224px;width:186px;height:48px;background:var(--white);border-radius:2px;color:var(--ink);font-family:"Arimo",Arial,sans-serif;font-weight:700;font-size:15px;display:flex;align-items:center;justify-content:center}

.section-tabs{position:absolute;top:506px;left:0;width:1041px;height:56px;background:var(--tab-dark);display:flex;padding-left:86px}
.tab{width:289px;height:56px;display:flex;align-items:center;justify-content:center;gap:12px;color:var(--white);font-family:"Arimo",Arial,sans-serif;font-weight:700;font-size:16px;border-right:1px solid var(--tab-line)}
.tab.active{background:var(--royal);border-right:1px solid var(--tab-dark)}

.about{position:absolute;top:606px;left:86px;width:870px}
.about h1{font-family:"Arimo",Arial,sans-serif;font-weight:700;font-size:32px;color:var(--ink);line-height:44px;margin-bottom:11px}
.about p{font-size:11px;line-height:26px;color:var(--body-text);margin-bottom:26px}

.site-footer{position:absolute;top:1119px;left:0;width:1041px;height:81px;background:var(--royal);color:var(--white)}
.footer-nav{position:absolute;left:87px;top:19px;font-size:11.6px;line-height:16px}
.footer-nav .sep{margin:0 7px}
.copyright{position:absolute;left:86px;top:43px;font-size:11.6px;line-height:16px}
.social{position:absolute;left:802px;top:24px;display:flex;gap:6px}
.social span{width:33px;height:33px;border:2px solid var(--white);border-radius:50%}
</style>
</head>
<body>
<header class="site-header">
  <div class="brand">BRIEFLY LEDGER</div>
  <div class="sign-in">
    <svg width="10" height="12" viewBox="0 0 10 12"><path d="M2.5 5V3.5a2.5 2.5 0 0 1 5 0V5" fill="none" stroke="#fff" stroke-width="1.6"/><rect x="0.5" y="5" width="9" height="7" rx="1" fill="#fff"/></svg>
    SIGN IN
  </div>
</header>

<section class="hero">
  <div class="hero-visual" role="img" aria-label="Aerial view of a coastal city skyline beside a blue bay"></div>
  <svg class="play" width="47" height="47" viewBox="0 0 47 47"><circle cx="23.5" cy="23.5" r="20.5" fill="none" stroke="#fff" stroke-width="5"/><circle cx="23.5" cy="23.5" r="13" fill="#fff"/><path d="M20 16.5 L30 23.5 L20 30.5Z" fill="var(--sea-deep)"/></svg>
  <div class="motto">OBSERVE NAVIGATE DECIDE</div>
  <div class="sign-up">SIGN UP NOW</div>
</section>

<nav class="section-tabs">
  <div class="tab active">
    <svg width="30" height="27" viewBox="0 0 30 27" fill="#fff"><circle cx="15" cy="7" r="5"/><circle cx="6" cy="5" r="3.5"/><circle cx="24" cy="5" r="3.5"/><path d="M7 27v-8a8 8 0 0 1 16 0v8z"/><path d="M0 19v-4a6 6 0 0 1 9-5 10 10 0 0 0-3 9z"/><path d="M30 19v-4a6 6 0 0 0-9-5 10 10 0 0 1 3 9z"/></svg>
    ABOUT US
  </div>
  <div class="tab">
    <svg width="30" height="22" viewBox="0 0 30 22" fill="none" stroke="#fff" stroke-width="1.8"><rect x="4" y="1" width="25" height="20"/><path d="M4 6H1v13a2 2 0 0 0 3 0"/><rect x="8" y="5" width="8" height="6" fill="#fff"/><path d="M19 6h7M19 10h7M8 14h18M8 17h18"/></svg>
    PRESS
  </div>
  <div class="tab">
    <svg width="27" height="20" viewBox="0 0 27 20" fill="#fff"><path d="M0 2a2 2 0 0 1 2-2h23a2 2 0 0 1 2 2v1L13.5 11 0 3z"/><path d="M0 6l13.5 8L27 6v12a2 2 0 0 1-2 2H2a2 2 0 0 1-2-2z"/></svg>
    CONTACT US
  </div>
</nav>

<main class="about">
  <h1>ABOUT US</h1>
  <p>Sed ut perspiciatis unde omnis iste natus error sit voluptatem accusantium doloremque laudantium, totam rem aperiam, eaque ipsa quae ab illo inventore veritatis et quasi archit ecto beatae vitae dicta sunt explicabo. Nemo enim ipsam voluptatem quia voluptas sit aspernatur aut odit aut fugit, sed quia consequuntur magni dolores eos qui ratione voluptatem sequi nesciu eque porro quisquam est, qui dolorem ipsum quia dolor sit amet.</p>
  <p>Consectetur, adipisci velit, sed quia non numquam eius modi tempora incidunt ut labore et dolore magnam aliquam quaerat voluptatem. Ut enim ad minima veniam, quis nostrum exercitationem ullam corporis suscipit laboriosam, nisi ut aliquid ex ea commodi consequatur? Quis autem vel eum iure reprehenderit qui in ea voluptate velit esse quam nihil mol estiae consequatur, vel illum qui dolorem eum fugiat quo voluptas nulla pariatur Nor again is there anyone who loves or pursues or desires to obtain pain of itself, because it is pain, but because occasionally circumstances occur in which toil and pain can procure him some great pleasure. To take a trivial example, which of us ever undertakes laborious physical exercise, except to obtain some advantage from it? But who has any right to find fault with a man who chooses to enjoy a pleasure that has no annoying consequences.</p>
  <p>At vero eos et accusamus et iusto odio dignissimos ducimus qui blanditiis praesentium voluptatum deleniti atque corrupti quos dolores et quas molestias excepturi sint occaecati cupiditate non provident, similique sunt in culpa qui officia deserunt mollitia animi, id est laborum et dolorum fuga. Et harum quidem rerum facilis est et expedita distinctio. m libero tempore, cum soluta nobis est eligendi optio cumque nihil impedit quo minus id quod maxime placeat facere possimus, omnis voluptas assumenda est, omnis dolor repellenut reiciendis voluptatibus maiores alias conseq.</p>
</main>

<footer class="site-footer">
  <div class="footer-nav">Home<span class="sep">|</span>About us<span class="sep">|</span>Press<span class="sep">|</span>Events<span class="sep">|</span>Contact Us</div>
  <div class="copyright">© 2016, Briefly ledger. All rights reserved.</div>
  <div class="social"><span></span><span></span><span></span><span></span></div>
</footer>
</body>
</html>
```